R7M Horizon Business Card Design

We need a business card created for our New Business "R7M Horizon"<br/><br/>The business card design is up to you however the following information must be on the business card:<br/><br/>Front of the business card -<br/>Email :darrenp@r7mhorizon.nz<br/>Mobile: +64 (0) 22 4870 619<br/>Website: www.r7mhorizon.nz<br/>Card Owner Name: Darren Paltrow<br/>Company Title: Business Development Manager<br/>Slogan: "The BEST of both worlds". <br/>Logo On the front attached to the design brief<br/><br/>On the back: <br/>Space on the back for 4 more versions of the logo across the bottom of the card indicating different subsidiary brands - R7M Coffee, R7M Arts, R7M ?? (The card will be used for all of these brands - We Will add the extra subsidiary logos to the design once the design is finished (We are a graphics design team). <br/><br/>Other than that we want a premium feeling logo that remains universally usable depending on the business entity that we are using the card for. The use of bright bold colours would be great but we still want the card to feel premium.
Target Market(s)
Gift Design and Manufacturing Companies
Contact Information for Business Card
Front of the business card -
Email :darrenp@r7mhorizon.nz
Mobile: +64 (0) 22 4870 619
Website: www.r7mhorizon.nz
Card Owner Name: Darren Paltrow
Company Title: Business Development Manager
Slogan: "The BEST of both worlds".
Logo On the front attached to the design brief

```html
<!DOCTYPE html>
<html lang="en">
<head>
<meta charset="UTF-8">
<title>R7M Horizon Business Card</title>
<link href="https://fonts.googleapis.com/css2?family=Open+Sans:wght@400;600;700;800&display=swap" rel="stylesheet">
<style>
  :root {
    --brand-blue: #3748a0;
    --ink: #3a3a3a;
    --paper: #ffffff;
    --backdrop: #e6e7ea;
  }
  * { margin: 0; padding: 0; box-sizing: border-box; }
  html, body {
    width: 1200px; height: 900px; overflow: hidden;
    background: var(--backdrop);
    font-family: "Open Sans", Arial, sans-serif;
  }
  .canvas { position: relative; width: 1200px; height: 900px; }
  .card {
    position: absolute; left: 285px; width: 630px; height: 360px;
    box-shadow: 0 6px 18px rgba(0,0,0,0.18);
  }
  .card-back { top: 50px; background: var(--brand-blue); }
  .card-front { top: 490px; background: var(--paper); }

  .brand-name {
    font-weight: 700; letter-spacing: 0.5px; white-space: nowrap;
  }
  .card-back .brand-name {
    position: absolute; left: 50%; top: 50%;
    transform: translate(-50%, -50%);
    color: var(--paper); font-size: 46px;
  }
  .card-front .brand-name {
    position: absolute; left: 48px; top: 52px;
    color: var(--brand-blue); font-size: 36px;
  }

  .holder { position: absolute; left: 60px; top: 150px; }
  .holder-name {
    color: var(--brand-blue); font-weight: 800; font-size: 25px;
    text-transform: uppercase; letter-spacing: 0.3px; line-height: 1.1;
  }
  .holder-title {
    color: var(--ink); font-size: 17px; margin-top: 2px; margin-left: 14px;
  }

  .contact-list {
    position: absolute; left: 78px; top: 238px; list-style: none;
    color: var(--ink); font-size: 17px; line-height: 26px;
  }
  .contact-list li { display: flex; align-items: center; gap: 9px; }
  .contact-list svg { width: 14px; height: 14px; flex: none; fill: var(--brand-blue); }

  .slogan {
    position: absolute; right: 34px; top: 262px;
    color: var(--brand-blue); font-size: 19px;
  }
  .slogan strong { font-weight: 800; }
  .slogan-bar {
    position: absolute; right: 0; top: 298px; width: 220px; height: 12px;
    background: var(--brand-blue);
  }
</style>
</head>
<body>
<main class="canvas">
  <section class="card card-back" aria-label="Card back">
    <p class="brand-name">R7M Horizon</p>
  </section>

  <section class="card card-front" aria-label="Card front">
    <p class="brand-name">R7M Horizon</p>

    <div class="holder">
      <h1 class="holder-name">Darren Paltrow</h1>
      <p class="holder-title">Business Development Manager</p>
    </div>

    <ul class="contact-list">
      <li>
        <svg viewBox="0 0 14 14" aria-hidden="true"><path d="M3 0h8a1 1 0 0 1 1 1v12a1 1 0 0 1-1 1H3a1 1 0 0 1-1-1V1a1 1 0 0 1 1-1zm.5 1.5v9h7v-9zM7 11.5a.9.9 0 1 0 0 1.8.9.9 0 0 0 0-1.8z"/></svg>
        +64 (0) 22 4870 619
      </li>
      <li>
        <svg viewBox="0 0 14 14" aria-hidden="true"><path d="M0 3h14v1L7 8 0 4zm0 2.3 7 4 7-4V11H0z"/></svg>
        darrenp@r7mhorizon.nz
      </li>
      <li>
        <svg viewBox="0 0 14 14" aria-hidden="true"><circle cx="7" cy="7" r="6.5"/><path d="M3 5c2 0 2 2 4 2s1 3 3 3" stroke="#fff" stroke-width="1.2" fill="none"/></svg>
        www.r7mhorizon.nz
      </li>
    </ul>

    <p class="slogan">The <strong>BEST</strong> of both worlds</p>
    <div class="slogan-bar"></div>
  </section>
</main>
</body>
</html>
```